Kelvaro.ch is looking for business card letterhead and envelope C5 with WOW effect

We need a strong business card for our company Kelvaro.ch, logo is available. You want a black or dark background on which the logo Stark r% 26 # 252; appears. Letterhead and envelope in C5 format should be in a similar design, but does not have to be We need a strong business card for our company Kelvaro.ch, logo is available. A black or dark background is desired, on which the logo Stark comes across. The letterhead and the envelope in C5 format should have a similar design.

Target Market(s)

Private customers as well as entrepreneurs

Contact Information for Business Card

E-mail: info@kelvaro-example.ch
Web.www.Kelvaro-example.ch
Tel: +41 ( 0 ) 79 482 6037
Adresse:
Lindenweg 14
9406 Tarnbach

Hier kann man Icons verwenden für Email,Tel und Adressse

Font styles to use
Other font styles liked:
• Dubai,bold

Colors

Designer to choose colors to be used in the design.

Requirements
Must have
• WOW effect
Nice to have
• R% 26 # 252; back business card with our service listings. - VEHICLE LABELING - SHOP WINDOW LABELING - STICKERS AND MUCH MORE ... in red color

```html
<!DOCTYPE html>
<html lang="en">
<head>
<meta charset="utf-8">
<title>Kelvaro.ch – Business Card</title>
<link href="https://fonts.googleapis.com/css2?family=Exo+2:wght@500;700;800&family=Ubuntu:wght@400;500&display=swap" rel="stylesheet">
<style>
  :root {
    --stage: #2a2a2c;
    --card-top: #1c2a4d;
    --card-bottom: #121c38;
    --white: #ffffff;
    --yellow: #fdd235;
    --red: #e0262b;
    --muted: #dfe3ee;
  }
  * { box-sizing: border-box; margin: 0; padding: 0; }
  html, body { width: 1200px; height: 930px; overflow: hidden; }
  body {
    background: var(--stage);
    position: relative;
    font-family: "Ubuntu", sans-serif;
  }
  .card {
    position: absolute;
    width: 600px;
    height: 360px;
    border-radius: 22px;
    background: linear-gradient(160deg, var(--card-top), var(--card-bottom));
    box-shadow: 0 18px 40px rgba(0,0,0,.45);
    overflow: hidden;
  }
  .card--front { left: 80px; top: 70px; }
  .card--back { left: 520px; top: 500px; }

  /* front */
  .wordmark {
    position: absolute;
    left: 110px; top: 110px;
    font-family: "Exo 2", sans-serif;
    font-weight: 800;
    font-size: 54px;
    letter-spacing: 1px;
    color: var(--white);
    text-transform: uppercase;
  }
  .services {
    position: absolute;
    right: 110px; top: 196px;
    list-style: none;
    text-align: right;
  }
  .services li {
    font-family: "Ubuntu", sans-serif;
    font-size: 15px;
    color: var(--white);
    line-height: 22px;
    text-transform: uppercase;
    display: flex; justify-content: flex-end; align-items: center; gap: 10px;
  }
  .services li::after {
    content: "";
    width: 8px; height: 8px;
    border: 2px solid var(--red);
    border-radius: 50%;
  }

  /* back */
  .person {
    position: absolute;
    left: 60px; top: 150px;
    width: 250px;
  }
  .person__name {
    font-family: "Exo 2", sans-serif;
    font-weight: 700;
    font-size: 31px;
    color: var(--white);
    text-transform: uppercase;
    white-space: nowrap;
  }
  .person__name .surname { color: var(--yellow); }
  .person__role {
    font-size: 16px;
    color: var(--muted);
    text-align: right;
    margin-top: 2px;
  }
  .divider {
    position: absolute;
    left: 330px; top: 110px;
    width: 2px; height: 140px;
    background: var(--yellow);
  }
  .contact {
    position: absolute;
    left: 352px; top: 112px;
    color: var(--white);
    font-size: 15px;
    line-height: 23px;
    list-style: none;
  }
  .contact li { display: flex; align-items: center; gap: 8px; }
  .contact svg { width: 14px; height: 14px; flex: none; }
  .contact .address { padding-left: 0; }
</style>
</head>
<body>
  <section class="card card--front" aria-label="Business card front">
    <div class="wordmark">Kelvaro.ch</div>
    <ul class="services">
      <li>Vehicle labeling</li>
      <li>Shop window labeling</li>
      <li>Stickers and much more</li>
    </ul>
  </section>

  <section class="card card--back" aria-label="Business card back">
    <div class="person">
      <div class="person__name">Marco <span class="surname">Brenner</span></div>
      <div class="person__role">Director</div>
    </div>
    <div class="divider"></div>
    <ul class="contact">
      <li class="address">Lindenweg 14</li>
      <li class="address">9406 Tarnbach</li>
      <li>
        <svg viewBox="0 0 24 24" aria-hidden="true"><path fill="#fdd235" d="M6.6 10.8a15 15 0 0 0 6.6 6.6l2.2-2.2c.3-.3.7-.4 1-.2 1.1.4 2.3.6 3.6.6.6 0 1 .4 1 1V20c0 .6-.4 1-1 1A17 17 0 0 1 3 4c0-.6.4-1 1-1h3.5c.6 0 1 .4 1 1 0 1.3.2 2.5.6 3.6.1.3 0 .7-.2 1z"/></svg>
        +41 ( 0 ) 79 482 6037
      </li>
      <li>
        <svg viewBox="0 0 24 24" aria-hidden="true"><rect x="3" y="5" width="18" height="14" rx="1.5" fill="none" stroke="#fdd235" stroke-width="2"/><path d="M3.5 6l8.5 7 8.5-7" fill="none" stroke="#fdd235" stroke-width="2"/></svg>
        info@kelvaro-example.ch
      </li>
      <li>
        <svg viewBox="0 0 24 24" aria-hidden="true"><circle cx="12" cy="12" r="9" fill="none" stroke="#fdd235" stroke-width="2"/><path d="M3 12h18M12 3c3 3 3 15 0 18M12 3c-3 3-3 15 0 18" fill="none" stroke="#fdd235" stroke-width="1.6"/></svg>
        www.kelvaro-example.ch
      </li>
    </ul>
  </section>
</body>
</html>
```